Copperleaf Roofing Business Card

This is my current business card. But I’d like to make some changes. Somewhere on the card I’d like to list some of the services we offer. Maybe on the back? But I’d still like to keep the red. White and black modern look.

-residential & commercial roofing
-Roof Repairs & Maintenance
-Storm Damage & Insurance Claims specialist
-Christmas Lights and permanent Christmas lights
Fencing. Windows. Gutters. Siding. Sheetrock, painting.

```html
<!DOCTYPE html>
<html lang="en">
<head>
<meta charset="utf-8">
<title>Copperleaf Roofing Co. – Business Card</title>
<link rel="stylesheet" href="https://fonts.googleapis.com/css2?family=Michroma&family=Roboto:wght@700&family=Lato:wght@400&display=swap">
<style>
  :root {
    --stage: #3a3a3c;
    --red: #e31b23;
    --red-deep: #8e0f14;
    --red-dark: #5a080b;
    --black: #111111;
    --white: #ffffff;
    --ink: #1a1a1a;
  }
  * { box-sizing: border-box; margin: 0; padding: 0; }
  html, body { width: 1200px; height: 694px; overflow: hidden; }
  body {
    background: var(--stage);
    position: relative;
    font-family: "Lato", sans-serif;
  }
  .card {
    position: absolute;
    top: 187px;
    width: 546px;
    height: 320px;
    border-radius: 18px;
    overflow: hidden;
  }
  .card--back { left: 36px; }
  .card--front { left: 618px; background: var(--white); }

  /* back side */
  .tartan-field {
    position: absolute; inset: 0;
    background: linear-gradient(135deg, var(--red-deep) 0%, var(--red) 38%, var(--red-dark) 62%, var(--red) 85%, var(--red-deep) 100%);
  }
  .back-lockup {
    position: absolute;
    left: 0; right: 0; top: 48px;
    display: flex; flex-direction: column; align-items: center; gap: 14px;
  }
  .mark-circle {
    width: 92px; height: 92px; border-radius: 50%;
    background: var(--black);
    border: 5px solid var(--white);
  }
  .brand-name {
    font-family: "Michroma", sans-serif;
    font-size: 25px;
    line-height: 1.15;
    text-align: center;
    letter-spacing: 1px;
  }
  .brand-name--light { color: var(--white); }
  .brand-name small { display: block; font-size: 17px; }
  .services {
    position: absolute;
    left: 26px; right: 26px; bottom: 22px;
    font-family: "Roboto", sans-serif;
    font-weight: 700;
    font-size: 12.5px;
    line-height: 1.5;
    color: var(--white);
    text-align: center;
  }

  /* front side */
  .tartan-band {
    position: absolute;
    right: 0; bottom: 0;
    width: 100%; height: 100%;
    background: linear-gradient(135deg, var(--red-deep), var(--red) 50%, var(--red-dark));
    clip-path: polygon(100% 62%, 100% 100%, 30% 100%, 33% 96%, 97% 96%, 97% 64%);
  }
  .front-lockup {
    position: absolute;
    left: 120px; top: 34px;
    display: flex; align-items: center; gap: 14px;
  }
  .front-lockup .mark-circle {
    width: 78px; height: 78px; border: none; background: var(--red);
  }
  .brand-name--red { color: var(--red); text-align: left; font-size: 22px; }
  .brand-name--red small { font-size: 15px; }
  .details {
    position: absolute;
    left: 60px; right: 40px; top: 178px;
    display: flex; align-items: center; gap: 24px;
  }
  .person { text-align: right; width: 200px; }
  .person-name {
    font-family: "Michroma", sans-serif;
    font-size: 19px;
    letter-spacing: 1px;
    color: var(--red);
  }
  .person-name .surname { color: var(--ink); }
  .person-role { font-size: 15px; color: var(--ink); margin-top: 4px; }
  .divider { width: 2px; height: 74px; background: var(--red); }
  .contacts { list-style: none; display: flex; flex-direction: column; gap: 6px; }
  .contacts li {
    display: flex; align-items: center; gap: 8px;
    font-size: 14px; color: var(--ink);
  }
  .contacts svg { width: 15px; height: 15px; flex: none; }
</style>
</head>
<body>

  <section class="card card--back" aria-label="Card back">
    <div class="tartan-field" role="img" aria-label="Red, black and white tartan pattern background"></div>
    <div class="back-lockup">
      <div class="mark-circle"></div>
      <p class="brand-name brand-name--light">COPPERLEAF<small>ROOFING CO.</small></p>
    </div>
    <p class="services">
      • Residential &amp; commercial roofing • Roof Repairs &amp; Maintenance • Storm Damage &amp;
      Insurance Claims specialist • Christmas Lights and permanent Christmas light
      • Fencing • Windows • Siding • Sheetrock • Painting
    </p>
  </section>

  <section class="card card--front" aria-label="Card front">
    <div class="tartan-band" role="img" aria-label="Red tartan pattern border band"></div>
    <div class="front-lockup">
      <div class="mark-circle"></div>
      <p class="brand-name brand-name--red">COPPERLEAF<small>ROOFING CO.</small></p>
    </div>
    <div class="details">
      <div class="person">
        <p class="person-name">DEAN <span class="surname">HARLOW</span></p>
        <p class="person-role">Owner</p>
      </div>
      <div class="divider"></div>
      <ul class="contacts">
        <li>
          <svg viewBox="0 0 24 24"><path fill="#e31b23" d="M6.6 10.8a15.1 15.1 0 0 0 6.6 6.6l2.2-2.2c.3-.3.7-.4 1-.2 1.1.4 2.3.6 3.6.6.6 0 1 .4 1 1V20c0 .6-.4 1-1 1A17 17 0 0 1 3 4c0-.6.4-1 1-1h3.5c.6 0 1 .4 1 1 0 1.3.2 2.5.6 3.6.1.3 0 .7-.2 1z"/></svg>
          555-014-2286
        </li>
        <li>
          <svg viewBox="0 0 24 24"><rect x="2" y="5" width="20" height="14" rx="1" fill="#e31b23"/><path d="M2 6l10 7 10-7" fill="none" stroke="#fff" stroke-width="1.8"/></svg>
          Dean@copperleafroofing.co
        </li>
        <li>
          <svg viewBox="0 0 24 24"><circle cx="12" cy="12" r="10" fill="#e31b23"/><ellipse cx="12" cy="12" rx="4" ry="10" fill="none" stroke="#fff" stroke-width="1.5"/><path d="M2 12h20" stroke="#fff" stroke-width="1.5"/></svg>
          www.copperleafroofing.co
        </li>
      </ul>
    </div>
  </section>

</body>
</html>
```